TA BRAMLEY BUSINESS CARD DESIGN PROJECT

We need to utilize our logo that was expertly created on PixelHarbor and now need to match this with a business card design.

```html
<!DOCTYPE html>
<html lang="en">
<head>
<meta charset="UTF-8">
<title>TA BRAMLEY – Business Card</title>
<link href="https://fonts.googleapis.com/css2?family=Open+Sans:wght@400;600;700&display=swap" rel="stylesheet">
<style>
  :root {
    --backdrop: #232323;
    --card-black: #1b1b1b;
    --brand-blue: #1557b0;
    --brand-blue-deep: #0f3f8f;
    --brand-blue-light: #2a6bd0;
    --ink-white: #ffffff;
    --ink-soft: #e6e6e6;
    --divider: #8a8a8a;
  }
  * { margin: 0; padding: 0; box-sizing: border-box; }
  html, body {
    width: 1200px; height: 780px; overflow: hidden;
    background: var(--backdrop);
    font-family: "Open Sans", Arial, sans-serif;
  }
  .canvas {
    position: relative; width: 1200px; height: 780px;
    display: flex; align-items: center; justify-content: center; gap: 50px;
  }
  .card {
    position: relative; width: 525px; height: 300px; overflow: hidden;
    box-shadow: 0 14px 30px rgba(0,0,0,0.55);
  }

  /* Front */
  .card-front { background: var(--card-black); }
  .front-brand {
    position: absolute; left: 34px; top: 62px;
    display: flex; align-items: center; gap: 10px;
    color: var(--brand-blue); font-weight: 700; font-size: 30px; letter-spacing: 3px;
  }
  .brand-square { width: 22px; height: 22px; background: var(--brand-blue); }
  .front-divider { position: absolute; left: 0; top: 0; }
  .contact-block { position: absolute; left: 300px; top: 92px; }
  .person-name { color: var(--brand-blue); font-weight: 700; font-size: 24px; line-height: 1.1; }
  .person-title { color: var(--ink-soft); font-size: 14px; margin-top: 2px; margin-bottom: 14px; }
  .contact-list { list-style: none; }
  .contact-item {
    display: flex; align-items: center; gap: 8px;
    color: var(--ink-white); font-size: 14px; line-height: 22px;
  }
  .contact-icon { width: 13px; height: 13px; flex: none; }
  .address-band {
    position: absolute; left: 0; bottom: 0; width: 100%; height: 34px;
    background: var(--brand-blue);
    display: flex; align-items: center; padding-left: 26px;
  }
  .address-text { color: var(--ink-white); font-size: 13px; }
  .band-end {
    position: absolute; right: 0; bottom: 0; width: 46px; height: 34px;
    background: var(--ink-white);
  }

  /* Back */
  .card-back { background: var(--brand-blue); }
  .back-pattern {
    position: absolute; inset: 0;
    background: linear-gradient(120deg, var(--brand-blue-deep) 0%, var(--brand-blue) 55%, var(--brand-blue-light) 100%);
    opacity: 0.9;
  }
  .back-brand {
    position: absolute; right: 40px; bottom: 34px;
    display: flex; align-items: center; gap: 8px;
    color: var(--ink-white); font-weight: 700; font-size: 18px; letter-spacing: 3px;
  }
  .back-brand .brand-square { width: 14px; height: 14px; background: var(--ink-white); }
</style>
</head>
<body>
<main class="canvas">
  <section class="card card-front" aria-label="Business card front">
    <div class="front-brand"><span class="brand-square"></span>TA BRAMLEY</div>
    <svg class="front-divider" width="525" height="300" viewBox="0 0 525 300">
      <line x1="262" y1="262" x2="300" y2="60" stroke="var(--divider)" stroke-width="1"/>
    </svg>
    <div class="contact-block">
      <div class="person-name">Marisol Quenby</div>
      <div class="person-title">Managing Director</div>
      <ul class="contact-list">
        <li class="contact-item">
          <svg class="contact-icon" viewBox="0 0 24 24"><path fill="var(--brand-blue)" d="M6.6 10.8a15.1 15.1 0 0 0 6.6 6.6l2.2-2.2a1 1 0 0 1 1-.25 11.4 11.4 0 0 0 3.6.57 1 1 0 0 1 1 1V20a1 1 0 0 1-1 1A17 17 0 0 1 3 4a1 1 0 0 1 1-1h3.5a1 1 0 0 1 1 1c0 1.25.2 2.45.57 3.6a1 1 0 0 1-.25 1z"/></svg>
          (555) 014-3092
        </li>
        <li class="contact-item">
          <svg class="contact-icon" viewBox="0 0 24 24"><rect x="2" y="5" width="20" height="14" rx="2" fill="var(--brand-blue)"/><path d="M3 6l9 7 9-7" fill="none" stroke="var(--card-black)" stroke-width="2"/></svg>
          hello@tabramley.com
        </li>
        <li class="contact-item">
          <svg class="contact-icon" viewBox="0 0 24 24"><circle cx="12" cy="12" r="10" fill="var(--brand-blue)"/><path d="M2 12h20M12 2c3 3 3 17 0 20M12 2c-3 3-3 17 0 20" fill="none" stroke="var(--card-black)" stroke-width="1.5"/></svg>
          www.tabramley.com
        </li>
      </ul>
    </div>
    <div class="address-band">
      <span class="address-text">418 Linden Row Suite 120 Brookfield, TX 75500</span>
    </div>
    <div class="band-end"></div>
  </section>

  <section class="card card-back" aria-label="Business card back">
    <div class="back-pattern" role="img" aria-label="Repeating brand pattern in deep blue tones fading lighter to the right"></div>
    <div class="back-brand"><span class="brand-square"></span>TA BRAMLEY</div>
  </section>
</main>
</body>
</html>
```